Business card design for my company.
I would like the card's background colour to be black. You can also see our web site to get an idea of our brand. https://www.tmwhomecrafting.com.au/
- Name
- Email

```html
<!DOCTYPE html>
<html lang="en">
<head>
<meta charset="utf-8">
<title>TMW Home Crafting – Business Card</title>
<link rel="stylesheet" href="https://fonts.googleapis.com/css2?family=Arimo:wght@400;700&display=swap">
<style>
  :root {
    --page: #e9e6e1;
    --card: #0b0c0c;
    --card-edge: #1a1c1c;
    --green: #3aa64a;
    --green-deep: #15934a;
    --white: #f4f5f4;
    --ghost: #1c1e1e;
  }
  * { box-sizing: border-box; margin: 0; padding: 0; }
  html, body { width: 1200px; height: 900px; overflow: hidden; }
  body {
    background: var(--page);
    font-family: "Arimo", Arial, sans-serif;
    position: relative;
  }
  .card {
    position: absolute;
    left: 320px;
    width: 560px;
    height: 320px;
    border-radius: 44px 0 44px 0;
    background: linear-gradient(135deg, var(--card-edge) 0%, var(--card) 60%);
    box-shadow: 0 10px 28px rgba(0,0,0,0.28);
    overflow: hidden;
  }
  .card--front { top: 110px; }
  .card--back { top: 470px; }

  .front__web {
    position: absolute;
    top: 34px;
    right: 40px;
    color: var(--green);
    font-size: 15px;
    font-weight: 700;
    letter-spacing: 1.5px;
  }
  .front__brand {
    position: absolute;
    left: 48px;
    bottom: 70px;
    display: flex;
    align-items: center;
    gap: 16px;
    white-space: nowrap;
  }
  .front__brand-mark {
    width: 40px;
    height: 40px;
    background: var(--green);
  }
  .front__brand-name {
    color: var(--green);
    font-size: 36px;
    font-weight: 700;
    letter-spacing: 1px;
    line-height: 1;
  }

  .back__ghost {
    position: absolute;
    right: -6px;
    bottom: -22px;
    color: var(--ghost);
    font-size: 110px;
    font-weight: 700;
    line-height: 1;
    letter-spacing: 2px;
  }
  .back__contact {
    position: absolute;
    left: 34px;
    top: 74px;
    width: 270px;
  }
  .back__name {
    color: var(--green);
    font-size: 19px;
    font-weight: 700;
    text-transform: uppercase;
  }
  .back__role {
    color: var(--white);
    font-size: 14px;
    margin-top: 3px;
  }
  .back__list {
    list-style: none;
    margin-top: 22px;
  }
  .back__list li {
    display: flex;
    align-items: center;
    gap: 9px;
    color: var(--white);
    font-size: 13.5px;
    margin-bottom: 8px;
  }
  .back__list svg { width: 15px; height: 15px; flex: none; }
  .back__rule {
    height: 1.5px;
    background: var(--green-deep);
    margin: 6px 0 8px;
  }
  .back__address {
    color: var(--white);
    font-size: 13.5px;
  }
  .back__brand {
    position: absolute;
    right: 36px;
    top: 118px;
    text-align: right;
    color: var(--white);
    font-size: 22px;
    font-weight: 700;
    letter-spacing: 2px;
    line-height: 1.35;
  }
</style>
</head>
<body>

<section class="card card--front" aria-label="Card front">
  <p class="front__web">www.tmwhomecrafting.com.au</p>
  <div class="front__brand">
    <span class="front__brand-mark"></span>
    <span class="front__brand-name">TMW HOME CRAFTING</span>
  </div>
</section>

<section class="card card--back" aria-label="Card back">
  <span class="back__ghost" aria-hidden="true">TMW</span>

  <div class="back__contact">
    <h1 class="back__name">Liam Harcourt</h1>
    <p class="back__role">General Manager</p>
    <ul class="back__list">
      <li>
        <svg viewBox="0 0 16 16" aria-hidden="true"><path fill="#3aa64a" d="M3.6 1.5l2.2 2.6-1.3 1.6c.9 2 2.5 3.7 4.6 4.7l1.6-1.3 2.7 2.2-1.2 2.2C7.6 13.7 2.5 8.6 1.3 2.7z"/></svg>
        0400 123 456
      </li>
      <li>
        <svg viewBox="0 0 16 16" aria-hidden="true"><rect x="1.5" y="3.5" width="13" height="9" fill="none" stroke="#3aa64a" stroke-width="1.5"/><path d="M1.5 3.5l6.5 5 6.5-5" fill="none" stroke="#3aa64a" stroke-width="1.5"/></svg>
        info@tmwhomecrafting.com.au
      </li>
      <li>
        <svg viewBox="0 0 16 16" aria-hidden="true"><g fill="none" stroke="#3aa64a" stroke-width="1.2"><circle cx="8" cy="8" r="6.5"/><ellipse cx="8" cy="8" rx="3" ry="6.5"/><path d="M1.5 8h13M2.6 4.5h10.8M2.6 11.5h10.8"/></g></svg>
        www.tmwhomecrafting.com.au
      </li>
    </ul>
    <div class="back__rule"></div>
    <p class="back__address">Kelmore Bay, Northvale, Australia</p>
  </div>

  <div class="back__brand">TMW<br>HOME CRAFTING</div>
</section>

</body>
</html>
```